Tri-fold Brochure for Law Firm

Double-sided brochure to be folded into 6 sides tri-fold brochure for an estate planning special for new parents or parents-to-be. Brochure will be placed in classes for new parents/young parents.

Target Market(s)

New Parents Aged 24-34

Industry/Entity Type

Law Firm

Font styles to use
Serif

Requirements
Must have
• The information provided in the word document.
Nice to have
• Highlight the phrase "for New Parents."
• You may use the color scheme from our website:
• http://k48.7dq.examplehostbox.com/

```html
<!DOCTYPE html>
<html lang="en">
<head>
<meta charset="utf-8">
<title>Harlow Legal – Estate Planning Special for New Parents</title>
<link rel="stylesheet" href="https://fonts.googleapis.com/css2?family=Cinzel:wght@400;700&family=Lato:wght@400;700&family=Lora:ital,wght@0,400;1,400&display=swap">
<style>
  :root {
    --espresso: #2a211d;
    --espresso-deep: #1c1613;
    --gold: #e8b43a;
    --gold-soft: #f2c85a;
    --cream: #efe6da;
    --paper: #ffffff;
    --ink: #2b2b2b;
    --muted: #7a7a7a;
    --slate: #4b4b4b;
    --slate-dark: #3a3a3a;
    --amber-photo: #b5652a;
    --amber-dark: #4a2a16;
  }
  * { box-sizing: border-box; margin: 0; padding: 0; }
  html, body { width: 1200px; height: 743px; overflow: hidden; background: #ffffff; }
  .brochure { display: flex; width: 1200px; height: 743px; }
  .panel { width: 400px; height: 743px; position: relative; overflow: hidden; }

  /* Inside-left panel */
  .panel--info { background: var(--espresso); color: var(--cream); font-family: "Lato", sans-serif; }
  .info-body { padding: 26px 34px 0; }
  .audience { font-family: "Cinzel", serif; color: var(--gold); font-size: 19px; line-height: 1.3; text-align: center; letter-spacing: .5px; }
  .price { display: table; margin: 12px auto 0; background: var(--paper); color: var(--espresso); font-family: "Cinzel", serif; font-size: 17px; padding: 4px 12px; }
  .question { font-family: "Lora", serif; font-style: italic; color: var(--gold); font-size: 17px; margin: 22px 0 8px; }
  .copy { font-size: 11.6px; line-height: 1.5; margin-bottom: 10px; }
  .gold-band { position: absolute; left: 0; right: 0; height: 14px; background: linear-gradient(var(--gold-soft), var(--gold)); }
  .panel--info .gold-band { top: 580px; }
  .photo-books { position: absolute; left: 0; right: 0; top: 594px; bottom: 0; background: linear-gradient(160deg, #e9dcc2 0%, #b78b52 45%, #5a3a1c 100%); }

  /* Middle panel */
  .panel--contact { background: var(--paper); font-family: "Lato", sans-serif; color: var(--ink); text-align: center; }
  .top-rule { height: 22px; background: var(--gold); }
  .deadline { font-size: 20px; font-weight: 700; line-height: 1.3; margin: 24px 30px 0; }
  .deadline em { color: var(--gold); font-style: normal; }
  .fine-print { font-size: 11px; color: var(--muted); line-height: 1.45; margin: 14px 34px 0; }
  .photo-keys { margin: 22px auto 0; width: 340px; height: 200px; background: radial-gradient(ellipse at center, #dcdcdc 0%, #f2f2f2 55%, #ffffff 100%); }
  .firm { margin-top: 18px; }
  .firm-mark { width: 46px; height: 46px; border-radius: 50%; background: var(--gold); margin: 0 auto 12px; }
  .firm-name { font-family: "Lato", sans-serif; font-weight: 700; font-size: 19px; color: var(--slate); letter-spacing: .5px; }
  .firm-rule { width: 240px; height: 1px; background: #c9c9c9; margin: 10px auto 12px; }
  .contact-list { list-style: none; width: 240px; margin: 0 auto; text-align: left; font-size: 11.5px; color: var(--slate); }
  .contact-list li { display: flex; align-items: flex-start; gap: 8px; margin-bottom: 6px; line-height: 1.35; }
  .contact-list svg { flex: 0 0 12px; margin-top: 1px; }
  .bottom-rule { position: absolute; left: 80px; right: 80px; bottom: 26px; height: 1px; background: #c9c9c9; }

  /* Cover panel */
  .panel--cover { background: var(--espresso-deep); }
  .cover-head { height: 96px; display: flex; align-items: center; justify-content: center; }
  .cover-mark { width: 48px; height: 48px; border-radius: 50%; background: var(--gold); }
  .photo-scales { position: absolute; left: 0; right: 0; top: 100px; height: 380px; border-top: 3px solid var(--paper); background: radial-gradient(ellipse at 45% 45%, #c9955a 0%, var(--amber-photo) 35%, var(--amber-dark) 100%); }
  .panel--cover .gold-band { top: 488px; }
  .cover-title { position: absolute; left: 0; right: 0; top: 514px; height: 150px; background: linear-gradient(var(--slate), var(--slate-dark)); text-align: center; padding-top: 16px; }
  .title-kicker { font-family: "Cinzel", serif; color: var(--gold); font-size: 22px; }
  .title-main { font-family: "Cinzel", serif; color: var(--paper); font-size: 30px; line-height: 1.15; }
  .tagline { font-family: "Lato", sans-serif; color: #cfcfcf; font-size: 10.5px; margin-top: 4px; }
  .call { font-family: "Lato", sans-serif; font-weight: 700; color: var(--gold); font-size: 21px; margin-top: 12px; letter-spacing: .5px; }
  .web { position: absolute; left: 0; right: 0; bottom: 0; height: 79px; display: flex; align-items: center; justify-content: center; font-family: "Lato", sans-serif; font-weight: 700; color: var(--paper); font-size: 15px; }
</style>
</head>
<body>
<main class="brochure">

  <section class="panel panel--info">
    <div class="info-body">
      <h2 class="audience">For parents-to-be and parents of children under 5 years old.</h2>
      <p class="price">$750 per couple</p>
      <h3 class="question">Why should every parent have a will?</h3>
      <p class="copy">Imagine how many people love your children. Would there be a fight over who would care for your children if you passed away without leaving instructions?</p>
      <p class="copy">Naming a guardian in your will helps avoid litigation that would cause additional stress to your children and loved ones. You can also name a back-up in the event that your first choice is unable or unwilling to serve as guardian.</p>
      <h3 class="question">What does the estate planning package include?</h3>
      <p class="copy">Our estate planning package includes a will, an advance medical directive, and a power of attorney. A will names a guardian for your children and gives instructions on how to distribute your probate property at death. An advance medical directive, also known as a living will, states directions regarding your healthcare decisions in the event that you can't make those decisions yourself. A power of attorney gives someone the ability to handle your financial affairs during your lifetime.</p>
    </div>
    <div class="gold-band"></div>
    <div class="photo-books" role="img" aria-label="Photo of open law books on a desk"></div>
  </section>

  <section class="panel panel--contact">
    <div class="top-rule"></div>
    <h2 class="deadline">New Parent Estate Planning program ends <em>12/31/17</em></h2>
    <p class="fine-print">Special does not apply to individuals with over $1 million net worth or particularly complex plans. Special does not include drafting trusts. Available to Maryland residents only.</p>
    <div class="photo-keys" role="img" aria-label="Faded photo of a set of keys"></div>
    <div class="firm">
      <div class="firm-mark"></div>
      <p class="firm-name">HARLOW LEGAL, LLC</p>
      <div class="firm-rule"></div>
      <ul class="contact-list">
        <li><svg width="12" height="12" viewBox="0 0 12 12"><path d="M6 0.5a4 4 0 0 0-4 4c0 3 4 7 4 7s4-4 4-7a4 4 0 0 0-4-4zm0 5.5a1.5 1.5 0 1 1 0-3 1.5 1.5 0 0 1 0 3z" fill="#e8b43a"/></svg><span>48 Linden Row, Suite 310,<br>Towson, MD 21204</span></li>
        <li><svg width="12" height="12" viewBox="0 0 12 12"><path d="M2.5 1l2 2.5-1 1.2a7 7 0 0 0 3.8 3.8l1.2-1 2.5 2-1.3 1.5C5 10.5 1.5 7 1 2.3z" fill="#e8b43a"/></svg><span>(410) 555-0142</span></li>
        <li><svg width="12" height="12" viewBox="0 0 12 12"><rect x="1" y="2.5" width="10" height="7" fill="#e8b43a"/><path d="M1 2.5l5 4 5-4" stroke="#fff" fill="none"/></svg><span>clara@harlow-legal.com</span></li>
        <li><svg width="12" height="12" viewBox="0 0 12 12"><rect x="1" y="4" width="10" height="5" fill="#e8b43a"/><rect x="3" y="1" width="6" height="3" fill="#e8b43a"/><rect x="3" y="8" width="6" height="3" fill="#e8b43a"/></svg><span>(410) 555-0187</span></li>
        <li><svg width="12" height="12" viewBox="0 0 12 12"><circle cx="6" cy="6" r="5" fill="none" stroke="#e8b43a" stroke-width="1.4"/><path d="M1 6h10M6 1c-3 3-3 7 0 10M6 1c3 3 3 7 0 10" stroke="#e8b43a" fill="none"/></svg><span>www.harlow-legal.com</span></li>
      </ul>
    </div>
    <div class="bottom-rule"></div>
  </section>

  <section class="panel panel--cover">
    <div class="cover-head"><div class="cover-mark"></div></div>
    <div class="photo-scales" role="img" aria-label="Photo of brass scales of justice on a warm blurred background"></div>
    <div class="gold-band"></div>
    <div class="cover-title">
      <p class="title-kicker">Estate Planning Special</p>
      <h1 class="title-main">FOR NEW PARENTS</h1>
      <p class="tagline">Sharing our experience to achieve your goals and dreams</p>
      <p class="call">CALL US NOW: (410) 555-0142</p>
    </div>
    <p class="web">www.harlow-legal.com</p>
  </section>

</main>
</body>
</html>
```